larkforge website

commerce website to sell cookeries, brackets, mailboxes and to show off homes built. Modern Steel in design see marlo cycles web page to be like: https://www.marlocycles-demo.com/en/ sorry its bright nest hosting word press divi

must be able to add products to page

Target Market(s)

mainly western states of U.S.

Industry/Entity Type

Building Product

Coding

Coded - Design and coding required

Number of Pages Required

3 page

Font styles to use
Sans Serif

Colors

Designer to choose colors to be used in the design.

Requirements
Must have
• customers to be able to order products from page
• bright nest hosting word press divi

```html
<!DOCTYPE html>
<html lang="en">
<head>
<meta charset="utf-8">
<title>Larkforge</title>
<link href="https://fonts.googleapis.com/css2?family=Open+Sans:wght@400;600;700;800&display=swap" rel="stylesheet">
<style>
:root{
  --navy:#344a7b;
  --navy-dark:#2b3e68;
  --orange:#f47a20;
  --page:#f1f1f1;
  --text:#2f2f2f;
  --muted:#444;
  --line:#c9c9c9;
  --footer-dark:#252525;
}
*{box-sizing:border-box;margin:0;padding:0}
html,body{width:1200px;height:2678px;overflow:hidden}
body{font-family:'Open Sans',sans-serif;background:var(--page);color:var(--text);position:relative}
a{color:inherit;text-decoration:none}
.wrap{width:1050px;margin:0 auto;position:relative}

.topbar{height:48px;background:#f4f4f4}
.topbar .wrap{display:flex;align-items:center;height:48px}
.shipping{color:var(--navy);font-weight:700;font-size:14px;letter-spacing:.4px;display:flex;align-items:center;gap:8px}
.call{margin-left:auto;font-weight:700;font-size:15px;display:flex;align-items:center;gap:8px}
.account{margin-left:38px;font-size:13px;display:flex;gap:14px;color:#333}

.header{height:117px;background:var(--navy);color:#fff}
.header .wrap{height:117px}
.brand{position:absolute;left:0;top:44px;display:flex;align-items:center;gap:10px;font-size:24px;font-weight:600;letter-spacing:.5px}
.brand .mark{width:26px;height:26px;border-radius:50%;background:#fff}
.search{position:absolute;left:504px;top:23px;display:flex}
.search input{width:322px;height:35px;border:0;padding:0 14px;font:13px 'Open Sans',sans-serif;color:#666}
.search button{width:47px;height:35px;border:0;background:var(--orange);display:flex;align-items:center;justify-content:center}
.cart{position:absolute;right:0;top:23px;display:flex;align-items:center;gap:12px;font-weight:700;font-size:13px}
.cart .bubble{width:37px;height:37px;border-radius:50%;background:var(--navy-dark);display:flex;align-items:center;justify-content:center}
.nav{position:absolute;right:0;top:74px;display:flex;font-size:13px;font-weight:700;letter-spacing:.4px}
.nav a{padding:8px 15px 13px;margin-left:14px}
.nav a:first-child{margin-left:0}
.nav a.active{color:var(--orange);border-bottom:5px solid var(--orange)}
.nav a:last-child{padding-right:0}

.hero{height:440px;position:relative;background:radial-gradient(ellipse at 50% 70%,#a4552a 0%,#4e3a2c 35%,#2d2a27 75%);display:flex;flex-direction:column;align-items:center;color:#fff}
.hero h1{margin-top:132px;font-size:54px;font-weight:700;letter-spacing:2px;line-height:1}
.hero p{font-size:25px;font-weight:600;letter-spacing:.5px;margin-top:6px}
.btn-shop{margin-top:14px;background:var(--orange);padding:8px 20px;font-size:15px;font-weight:700;letter-spacing:.8px}
.dots{position:absolute;top:390px;left:563px;display:flex;gap:10px}
.dots span{width:11px;height:11px;border-radius:50%;background:#bbb}
.dots span:first-child{background:#555}

.section-head{display:flex;align-items:baseline;gap:24px}
.section-head h2{font-size:27px;font-weight:700;letter-spacing:1px;color:#333}
.section-head a{color:var(--orange);font-weight:700;font-size:13px}
.products{position:relative}
.grid{display:grid;grid-template-columns:repeat(4,248px);justify-content:space-between;margin-top:24px}
.card{background:#fff;height:390px;display:flex;flex-direction:column;align-items:center;padding-top:18px;text-align:center}
.card .photo{width:212px;height:180px;background:radial-gradient(circle at 50% 45%,#6a6f78 0%,#2e3238 45%,#f3f3f3 72%)}
.card .photo.grill{background:linear-gradient(#e9cdb2 0 25%,#2a2d33 25% 45%,#f1ece4 45% 88%,#d9dadd 88%)}
.card h3{margin-top:26px;font-size:14px;font-weight:700;letter-spacing:.3px}
.card .desc{font-size:15px;color:var(--muted);line-height:22px;width:180px;margin-top:2px}
.card .price{color:var(--orange);font-weight:700;font-size:16px;margin-top:4px}
.btn-cart{margin-top:18px;background:var(--navy);color:#fff;font-size:12px;font-weight:700;letter-spacing:.6px;width:115px;height:35px;display:flex;align-items:center;justify-content:center}
.arrow{position:absolute;top:170px;width:34px;height:54px;background:#fff;border:1px solid #ccc;display:flex;align-items:center;justify-content:center}
.arrow.prev{left:-49px}.arrow.next{right:-49px}
.divider{border:0;border-top:1px solid var(--line)}

.newsletter{position:absolute;top:2239px;left:0;width:1200px;height:115px;background:var(--navy);color:#fff}
.newsletter .copy{position:absolute;right:662px;top:24px;text-align:right}
.newsletter h4{font-size:19px;font-weight:700;letter-spacing:.8px}
.newsletter p{font-size:15px;line-height:22px;margin-top:2px}
.newsletter form{position:absolute;left:563px;top:38px;display:flex;gap:9px}
.newsletter input{width:243px;height:39px;border:0;padding:0 13px;font:13px 'Open Sans',sans-serif}
.newsletter button{width:90px;height:39px;border:0;background:var(--orange);color:#fff;font:700 12px 'Open Sans',sans-serif;letter-spacing:.6px}

.footer{position:absolute;top:2354px;left:0;width:1200px;height:256px;background:var(--page)}
.footer .col{position:absolute;top:42px}
.footer h5{font-size:19px;font-weight:700;letter-spacing:.6px;color:#333;margin-bottom:8px}
.footer li{list-style:none;font-size:14px;line-height:27.5px;color:#333}
.social{display:flex;gap:16px;margin-top:14px}
.social span{width:26px;height:26px;border-radius:5px;background:#555}

.bottombar{position:absolute;top:2610px;left:0;width:1200px;height:68px;background:var(--footer-dark);color:#eee}
.bottombar .legal{position:absolute;left:77px;top:25px;font-size:12.5px}
.cards{position:absolute;right:75px;top:20px;display:flex;gap:16px}
.cards span{width:43px;height:28px;border-radius:4px;background:#e8e8e8;color:#333;font-size:9px;font-weight:700;display:flex;align-items:center;justify-content:center}
</style>
</head>
<body>

<div class="topbar"><div class="wrap">
  <div class="shipping"><svg width="16" height="12" viewBox="0 0 16 12"><rect x="0" y="1" width="10" height="8" fill="#f47a20"/><path d="M10 3h3l3 3v3h-6z" fill="#f47a20"/><circle cx="4" cy="10" r="2" fill="#f47a20"/><circle cx="12" cy="10" r="2" fill="#f47a20"/></svg>FREE SHIPPING</div>
  <div class="call"><svg width="12" height="12" viewBox="0 0 12 12"><path d="M2 0l2.5 2.8-1.2 1.6a7 7 0 0 0 4.3 4.3l1.6-1.2L12 10l-1.6 2C5 12 0 7 0 1.6z" fill="#333"/></svg>Call Us: 1-800-555-0147</div>
  <div class="account"><a href="#">Log in</a><span>I</span><a href="#">Register</a><span>I</span><a href="#">Favourite</a></div>
</div></div>

<header class="header"><div class="wrap">
  <div class="brand"><span class="mark"></span>LARKFORGE</div>
  <form class="search"><input type="text" placeholder="Search..."><button type="button" aria-label="Search"><svg width="16" height="16" viewBox="0 0 16 16"><circle cx="6.5" cy="6.5" r="5" fill="none" stroke="#fff" stroke-width="2.2"/><path d="M10 10l5 5" stroke="#fff" stroke-width="2.4"/></svg></button></form>
  <div class="cart"><span class="bubble"><svg width="16" height="14" viewBox="0 0 16 14"><path d="M0 1h3l2 8h9l2-6H4" fill="none" stroke="#fff" stroke-width="1.8"/><circle cx="6" cy="12" r="1.5" fill="#fff"/><circle cx="13" cy="12" r="1.5" fill="#fff"/></svg></span>MY CART (0)</div>
  <nav class="nav"><a class="active" href="#">HOME</a><a href="#">ABOUT</a><a href="#">PRODUCTS</a><a href="#">REVIEWS</a><a href="#">BLOG</a><a href="#">SHOP</a><a href="#">CONTACT US</a></nav>
</div></header>

<section class="hero" role="img" aria-label="Friends gathered around a steel fire pit at night">
  <h1>LARKFORGE</h1>
  <p>Praesent et magna ullamcorper</p>
  <a class="btn-shop" href="#">SHOP NOW</a>
  <div class="dots"><span></span><span></span><span></span><span></span></div>
</section>

<section class="wrap products" style="margin-top:50px">
  <div class="section-head"><h2>FEATURED PRODUCTS</h2><a href="#">SEE MORE</a></div>
  <div class="grid">
    <div class="card"><div class="photo" role="img" aria-label="Mesh-domed fire pit on legs"></div><h3>PRODUCT NAME</h3><p class="desc">Morbi id nulla vitae odio accumsan</p><p class="price">$49.59</p><a class="btn-cart" href="#">ADD TO CART</a></div>
    <div class="card"><div class="photo" role="img" aria-label="Black enamel roaster with rack"></div><h3>PRODUCT NAME</h3><p class="desc">Morbi id nulla vitae odio accumsan</p><p class="price">$49.59</p><a class="btn-cart" href="#">ADD TO CART</a></div>
    <div class="card"><div class="photo grill" role="img" aria-label="Round tabletop charcoal grill"></div><h3>PRODUCT NAME</h3><p class="desc">Morbi id nulla vitae odio accumsan</p><p class="price">$49.59</p><a class="btn-cart" href="#">ADD TO CART</a></div>
    <div class="card"><div class="photo" role="img" aria-label="Bowl fire pit on scrolled base"></div><h3>PRODUCT NAME</h3><p class="desc">Morbi id nulla vitae odio accumsan</p><p class="price">$49.59</p><a class="btn-cart" href="#">ADD TO CART</a></div>
  </div>
  <a class="arrow prev" href="#" aria-label="Previous"><svg width="10" height="18" viewBox="0 0 10 18"><path d="M9 1L1 9l8 8" fill="none" stroke="#333" stroke-width="1.6"/></svg></a>
  <a class="arrow next" href="#" aria-label="Next"><svg width="10" height="18" viewBox="0 0 10 18"><path d="M1 1l8 8-8 8" fill="none" stroke="#333" stroke-width="1.6"/></svg></a>
</section>

<div class="wrap" style="margin-top:58px"><hr class="divider"></div>

<section class="wrap products" style="margin-top:36px">
  <div class="section-head"><h2>NEW ARRIVALS</h2><a href="#">SEE MORE</a></div>
  <div class="grid">
    <div class="card"><div class="photo" role="img" aria-label="Bowl fire pit on scrolled base"></div><h3>PRODUCT NAME</h3><p class="desc">Morbi id nulla vitae odio accumsan</p><p class="price">$49.59</p><a class="btn-cart" href="#">ADD TO CART</a></div>
    <div class="card"><div class="photo grill" role="img" aria-label="Round tabletop charcoal grill"></div><h3>PRODUCT NAME</h3><p class="desc">Morbi id nulla vitae odio accumsan</p><p class="price">$49.59</p><a class="btn-cart" href="#">ADD TO CART</a></div>
    <div class="card"><div class="photo" role="img" aria-label="Mesh-domed fire pit on legs"></div><h3>PRODUCT NAME</h3><p class="desc">Morbi id nulla vitae odio accumsan</p><p class="price">$49.59</p><a class="btn-cart" href="#">ADD TO CART</a></div>
    <div class="card"><div class="photo grill" role="img" aria-label="Round tabletop charcoal grill"></div><h3>PRODUCT NAME</h3><p class="desc">Morbi id nulla vitae odio accumsan</p><p class="price">$49.59</p><a class="btn-cart" href="#">ADD TO CART</a></div>
  </div>
  <a class="arrow prev" href="#" aria-label="Previous"><svg width="10" height="18" viewBox="0 0 10 18"><path d="M9 1L1 9l8 8" fill="none" stroke="#333" stroke-width="1.6"/></svg></a>
  <a class="arrow next" href="#" aria-label="Next"><svg width="10" height="18" viewBox="0 0 10 18"><path d="M1 1l8 8-8 8" fill="none" stroke="#333" stroke-width="1.6"/></svg></a>
</section>

<div class="wrap" style="margin-top:53px"><hr class="divider"></div>

<section class="wrap products" style="margin-top:36px">
  <div class="section-head"><h2>BEST SELLERS</h2><a href="#">SEE MORE</a></div>
  <div class="grid">
    <div class="card"><div class="photo" role="img" aria-label="Bowl fire pit on scrolled base"></div><h3>PRODUCT NAME</h3><p class="desc">Morbi id nulla vitae odio accumsan</p><p class="price">$49.59</p><a class="btn-cart" href="#">ADD TO CART</a></div>
    <div class="card"><div class="photo" role="img" aria-label="Mesh-domed fire pit on legs"></div><h3>PRODUCT NAME</h3><p class="desc">Morbi id nulla vitae odio accumsan</p><p class="price">$49.59</p><a class="btn-cart" href="#">ADD TO CART</a></div>
    <div class="card"><div class="photo grill" role="img" aria-label="Round tabletop charcoal grill"></div><h3>PRODUCT NAME</h3><p class="desc">Morbi id nulla vitae odio accumsan</p><p class="price">$49.59</p><a class="btn-cart" href="#">ADD TO CART</a></div>
    <div class="card"><div class="photo" role="img" aria-label="Bowl fire pit on scrolled base"></div><h3>PRODUCT NAME</h3><p class="desc">Morbi id nulla vitae odio accumsan</p><p class="price">$49.59</p><a class="btn-cart" href="#">ADD TO CART</a></div>
  </div>
  <a class="arrow prev" href="#" aria-label="Previous"><svg width="10" height="18" viewBox="0 0 10 18"><path d="M9 1L1 9l8 8" fill="none" stroke="#333" stroke-width="1.6"/></svg></a>
  <a class="arrow next" href="#" aria-label="Next"><svg width="10" height="18" viewBox="0 0 10 18"><path d="M1 1l8 8-8 8" fill="none" stroke="#333" stroke-width="1.6"/></svg></a>
</section>

<section class="newsletter">
  <div class="copy"><h4>NEWSLETTER SIGN UP</h4><p>Morbi id nulla vitae odio accumsan<br>eleifend ut et libero</p></div>
  <form><input type="email" placeholder="Email Address"><button type="button">SIGN UP</button></form>
</section>

<footer class="footer">
  <div class="col" style="left:75px"><h5>About Us</h5><ul><li>Morbi id nulla</li><li>Vitae odio accumsan</li><li>Eleifend</li><li>Liberosed leo</li><li>Interdum</li><li>Convallis</li></ul></div>
  <div class="col" style="left:322px"><h5>My Account</h5><ul><li>Morbi id nulla</li><li>Vitae odio accumsan</li><li>Eleifend</li><li>Liberosed leo</li></ul></div>
  <div class="col" style="left:614px"><h5>Here to Help</h5><ul><li>Morbi id nulla</li><li>Vitae odio accumsan</li><li>Eleifend</li><li>Liberosed leo</li><li>Interdum</li></ul></div>
  <div class="col" style="left:903px"><h5>Social Media</h5><div class="social"><span aria-label="Social link"></span><span aria-label="Social link"></span><span aria-label="Social link"></span><span aria-label="Social link"></span></div></div>
</footer>

<div class="bottombar">
  <p class="legal">Copyright © 2020 Company Name. All Right Reserved</p>
  <div class="cards"><span>Quelp</span><span>Merix</span><span>Vondo</span><span>Daxel</span></div>
</div>

</body>
</html>
```